School Poster and Prompt Design

I would like posters created for each of our school values (from the attached Way of Working document). In these posters I would like our logo, and some graphics or pictures - you can use the strategic plan attached for some examples.

I would also like a Code of Conduct Prompt for teachers and students (smaller design that can be used as a sticker for a laptop) based on the attached Tallowmere Heights Basics document. I have also attached a photo example, which we quite like that can be used for a base. This document is called example classroom management prompts.

Target Market(s)

School and students

Requirements
Must have
• Logo built into the design
Our school motto at the bottom 'Strive to Accomplish'
Design that incorporates elements that relate to each of the values.
Design that looks and feels like the example. In our school colours.
Nice to have
• Posters - Easy to read and understand from a distance.
Prompt - Easy to read and understand if turned into a sticker for a laptop.

```html
<!DOCTYPE html>
<html lang="en">
<head>
<meta charset="utf-8">
<title>Classroom Routines – Tallowmere Heights High School</title>
<link rel="stylesheet" href="https://fonts.googleapis.com/css2?family=Roboto:wght@300;400;500;700;900&display=swap">
<style>
  :root {
    --navy: #16174a;
    --royal: #0b5596;
    --deep: #0b4f9c;
    --mid: #1e88c8;
    --sky: #29bdee;
    --cyan: #29a8df;
    --white: #ffffff;
    --backdrop: #d4d6d8;
  }
  * { box-sizing: border-box; margin: 0; padding: 0; }
  html, body { width: 1019px; height: 1200px; overflow: hidden; }
  body { background: var(--backdrop); font-family: "Roboto", sans-serif; position: relative; }

  .poster { position: absolute; left: 88px; top: 5px; width: 842px; height: 1190px; background: var(--white); overflow: hidden; box-shadow: 0 2px 8px rgba(0,0,0,.25); }
  .abs { position: absolute; }
  .center { text-align: center; }

  .header { left: 0; top: 22px; width: 842px; height: 166px; background: linear-gradient(90deg, #1c5ea6 0%, #1b3f82 35%, var(--navy) 60%); }
  .school-mark { left: 30px; top: 58px; width: 220px; display: flex; align-items: center; gap: 10px; }
  .school-mark .dot { width: 26px; height: 26px; border-radius: 50%; background: var(--sky); flex: none; }
  .school-mark .name { color: var(--white); font-weight: 500; font-size: 19px; line-height: 1.2; }
  .title { left: 250px; top: 64px; width: 470px; color: var(--white); font-weight: 300; font-size: 37px; letter-spacing: 1px; text-align: center; }
  .subtitle { left: 250px; top: 120px; width: 470px; color: var(--cyan); font-size: 21px; text-align: center; }

  .values { left: 0; top: 199px; width: 842px; color: var(--mid); font-size: 20px; text-align: center; padding-left: 110px; }
  .values .sep { margin: 0 14px; font-size: 14px; vertical-align: 2px; }

  .entry { left: 27px; top: 240px; width: 788px; height: 237px; background: var(--mid); border-radius: 3px; }
  .notch-down { width: 0; height: 0; border-left: 18px solid transparent; border-right: 18px solid transparent; border-top: 14px solid var(--white); }
  .entry-notch { left: 379px; top: 0; }
  .entry h2 { position: absolute; left: 0; top: 18px; width: 100%; text-align: center; color: var(--white); font-weight: 700; font-size: 50px; letter-spacing: 1px; }
  .entry-card { top: 79px; width: 230px; height: 141px; border-radius: 3px; color: var(--white); padding: 34px 0 0 26px; }
  .entry-card.light { background: var(--sky); }
  .entry-card.dark { background: var(--royal); padding-left: 52px; }
  .entry-card h3 { font-weight: 700; font-size: 16px; letter-spacing: .5px; margin-bottom: 8px; }
  .entry-card ul { list-style: none; font-size: 13px; line-height: 18px; }
  .entry-card li::before { content: "•"; margin-right: 9px; font-size: 10px; }

  .lesson-frame { left: 23px; top: 497px; width: 795px; height: 215px; border: 3px dotted #3a8fd0; }
  .attend-badge { left: 17px; top: 525px; width: 132px; height: 132px; border-radius: 50%; background: radial-gradient(circle at 50% 40%, #2cb8ea, #1a7cc4); border: 3px solid var(--white); box-shadow: 0 0 0 2px #1a7cc4; color: var(--white); font-size: 11px; line-height: 13.5px; display: flex; align-items: center; justify-content: center; text-align: center; padding: 0 18px; }
  .lesson-title { left: 160px; top: 526px; width: 520px; color: var(--deep); font-weight: 700; font-size: 44px; letter-spacing: 1px; text-align: center; }
  .lesson-sub { left: 160px; top: 585px; width: 520px; color: var(--mid); font-size: 16px; text-align: center; letter-spacing: .3px; }
  .check-item { width: 240px; text-align: center; }
  .check-item svg { display: block; margin: 0 auto 14px; }
  .lesson .check-item span { color: var(--deep); font-size: 16px; }

  .exit { left: 0; top: 742px; width: 842px; height: 235px; background: var(--royal); }
  .exit-notch { left: 406px; top: 977px; width: 0; height: 0; border-left: 18px solid transparent; border-right: 18px solid transparent; border-top: 16px solid var(--royal); }
  .exit h2 { position: absolute; left: 0; top: 18px; width: 100%; text-align: center; color: var(--white); font-weight: 700; font-size: 50px; letter-spacing: 1px; }
  .exit-sub { left: 0; top: 84px; width: 100%; text-align: center; color: var(--sky); font-size: 20px; }
  .exit .check-item span { color: var(--white); font-size: 14px; line-height: 17px; display: block; }

  .recognise { left: 0; top: 1008px; width: 842px; height: 42px; background: linear-gradient(90deg, var(--sky) 0%, #1e7ac0 55%, var(--royal) 100%); color: var(--white); font-size: 19px; text-align: center; line-height: 42px; }
  .reward { width: 260px; text-align: center; color: var(--deep); font-size: 17px; line-height: 20px; }
  .reward svg { display: block; margin: 0 auto; }
</style>
</head>
<body>
<main class="poster">
  <header class="header abs">
    <div class="school-mark abs"><span class="dot"></span><span class="name">Tallowmere Heights High School</span></div>
    <h1 class="title abs">CLASSROOM ROUTINES</h1>
    <p class="subtitle abs">WAY OF WORKING</p>
  </header>

  <p class="values abs">RESPECT<span class="sep">•</span>INDUSTRY<span class="sep">•</span>COOPERATION</p>

  <section class="entry abs">
    <div class="notch-down abs entry-notch"></div>
    <h2>ENTRY</h2>
    <div class="entry-card light abs" style="left:21px">
      <h3>COMMITMENT</h3>
      <ul><li>On time</li><li>Correct uniform</li><li>Ready to learning</li></ul>
    </div>
    <div class="entry-card dark abs" style="left:278px">
      <h3>COURTESY</h3>
      <ul><li>In line</li><li>Waiting quietly</li><li>Stand behind chairs</li></ul>
    </div>
    <div class="entry-card light abs" style="left:534px;padding-left:58px">
      <h3>COOPERATION</h3>
      <ul><li>In the right seat</li><li>Ready to participate</li><li>Actively listening</li></ul>
    </div>
  </section>

  <section class="lesson">
    <div class="lesson-frame abs"></div>
    <div class="attend-badge abs">Mark RollMark in the first 15 minutes and confirm with head count</div>
    <h2 class="lesson-title abs">START OF LESSON</h2>
    <p class="lesson-sub abs">SHOW AND EXPLAIN TO STUDENTS</p>
    <div class="check-item abs" style="left:62px;top:632px">
      <svg width="30" height="28" viewBox="0 0 30 28"><circle cx="13" cy="15" r="11" fill="none" stroke="#1e88c8" stroke-width="2"/><path d="M8 14l5 6L27 3" fill="none" stroke="#29bdee" stroke-width="2.5"/></svg>
      <span>LESSON INTENTION</span>
    </div>
    <div class="check-item abs" style="left:300px;top:632px">
      <svg width="30" height="28" viewBox="0 0 30 28"><circle cx="13" cy="15" r="11" fill="none" stroke="#1e88c8" stroke-width="2"/><path d="M8 14l5 6L27 3" fill="none" stroke="#29bdee" stroke-width="2.5"/></svg>
      <span>SUCCESS CRITERIA</span>
    </div>
    <div class="check-item abs" style="left:537px;top:632px">
      <svg width="30" height="28" viewBox="0 0 30 28"><circle cx="13" cy="15" r="11" fill="none" stroke="#1e88c8" stroke-width="2"/><path d="M8 14l5 6L27 3" fill="none" stroke="#29bdee" stroke-width="2.5"/></svg>
      <span>WAY OF WORKING FOCUS</span>
    </div>
  </section>

  <section class="exit abs">
    <h2>EXIT</h2>
    <p class="exit-sub abs">EXIT STRATEGY USED TO CHECK FOR UNDERSTANDING</p>
    <div class="check-item abs" style="left:62px;top:132px">
      <svg width="30" height="28" viewBox="0 0 30 28"><circle cx="13" cy="15" r="11" fill="none" stroke="#8fd8f5" stroke-width="2"/><path d="M8 14l5 6L27 3" fill="none" stroke="#29bdee" stroke-width="2.5"/></svg>
      <span style="margin-top:12px">IT IS CHECKED</span>
    </div>
    <div class="check-item abs" style="left:300px;top:132px">
      <svg width="30" height="28" viewBox="0 0 30 28"><circle cx="13" cy="15" r="11" fill="none" stroke="#8fd8f5" stroke-width="2"/><path d="M8 14l5 6L27 3" fill="none" stroke="#29bdee" stroke-width="2.5"/></svg>
      <span>ENVIRONMENT LEFT<br>NEAT AND TIDY</span>
    </div>
    <div class="check-item abs" style="left:537px;top:132px">
      <svg width="30" height="28" viewBox="0 0 30 28"><circle cx="13" cy="15" r="11" fill="none" stroke="#8fd8f5" stroke-width="2"/><path d="M8 14l5 6L27 3" fill="none" stroke="#29bdee" stroke-width="2.5"/></svg>
      <span>DOORS AND<br>WINDOWS LOCKED</span>
    </div>
  </section>
  <div class="exit-notch abs"></div>

  <p class="recognise abs">RECOGNISE POSITIVE BEHAVIOUR BY:</p>

  <div class="reward abs" style="left:44px;top:1070px">
    <svg width="56" height="62" viewBox="0 0 56 62"><path d="M4 28L28 6l24 22" fill="none" stroke="#1e88c8" stroke-width="6" stroke-linejoin="round"/><path d="M12 30v22h32V30L28 16z" fill="#16174a"/><path d="M27 30a4 4 0 018 0v12l6 1a5 5 0 014 6l-3 11H28l-8-12a3 3 0 015-4l2 2z" fill="#1e88c8" stroke="#fff" stroke-width="1.5"/></svg>
    <p style="margin-top:22px">Assigning house points</p>
  </div>
  <div class="reward abs" style="left:294px;top:1068px">
    <svg width="54" height="56" viewBox="0 0 54 56"><rect x="10" y="2" width="34" height="30" fill="#1e88c8"/><rect x="32" y="6" width="7" height="8" fill="#fff"/><path d="M2 26l25 18 25-18v28H2z" fill="#16174a"/><path d="M2 54l25-16 25 16" fill="none" stroke="#fff" stroke-width="1.5"/></svg>
    <p style="margin-top:12px">Postcard or<br>Student of the Week</p>
  </div>
  <div class="reward abs" style="left:588px;top:1070px">
    <svg width="50" height="54" viewBox="0 0 50 54"><path d="M6 22c0 14 12 27 26 28l5-7-8-6-4 4c-5-3-9-8-11-13l4-4-6-8z" fill="#16174a"/><circle cx="35" cy="14" r="11" fill="#fff" stroke="#1e88c8" stroke-width="2.5"/><path d="M29 15l6-6 6 6v5H29z" fill="#16174a"/></svg>
    <p style="margin-top:22px">Phone call home</p>
  </div>
</main>
</body>
</html>
```